New label design for Vitmain Water beverage

This is to create a new label for a vitamin water company called Qirna Vitamin. The label should be in dual languages. English and Arabic as seen attached for a previous example. You do not have to create an Arabic logo, just make space for it and I will have someon else do it. If you think you can do it, go ahead. I have also attached the bottle dimensions we are thinking of using. Please provide a new bottle design if you see fit. Please remember the bottle size is 400ml, and no pressure If I don't get a great bottle design, then I will use the attached one in that case. Please make the label diverse for various flavors, so it would apply easily and color print friendly. The brand is healthy, sporty, low or no sugars, no artificial flavors and no artificial coloring. All vitamins, minirals and electrolytes are healthy and real. Three flavors: pomogranite cherry, tropical citrus, and kiwi strawberry. So, each label would have different vitamins and offers unique components. Make it hip, trendy yet classy.
Good Luck!!!
Updates

Project Deadline Extended Reason: Because I updated a new file image example to follow and innovate from. Added Monday, February 02, 2015

Posted new file image example to follow and innovate from. Thanks, Added Monday, February 02, 2015

Target Market(s)

Age 15-40 males and females

Industry/Entity Type

Water Company

Requirements
Nice to have
• Plastic PET bottle design
• a 500 ml version

```html
<!DOCTYPE html>
<html lang="en">
<head>
<meta charset="utf-8">
<title>Qirna Vitamin – Label Design</title>
<link rel="stylesheet" href="https://fonts.googleapis.com/css2?family=Oswald:wght@500;700&family=Share+Tech+Mono&family=Cairo:wght@700&display=swap">
<style>
  :root{
    --bg:#e4e4e4;
    --ink:#111111;
    --grey:#6b6b6b;
    --leaf:#76a325;
    --leaf-dark:#3f7a1c;
    --lime-soft:#d3e3a4;
    --lime-pale:#e7f0cc;
    --label:#ffffff;
  }
  *{box-sizing:border-box;margin:0;padding:0}
  html,body{width:1200px;height:1000px;overflow:hidden}
  body{background:var(--bg);position:relative;font-family:"Oswald",sans-serif;color:var(--ink)}

  .title-block{position:absolute;left:48px;top:58px}
  .title-block .heading{font-weight:700;font-size:32px;line-height:1}
  .title-block .kicker{font-family:"Share Tech Mono",monospace;font-size:20px;letter-spacing:4px;margin:10px 0 0 18px}
  .brand-line{display:flex;align-items:center;gap:10px;margin-top:4px}
  .brand-line .dot{width:14px;height:14px;border-radius:50%;background:var(--leaf)}
  .brand-line .name{font-weight:700;font-size:46px;color:var(--leaf);line-height:1.1}
  .title-block .flavour-tag{font-weight:700;font-size:22px;color:var(--grey);margin-top:4px}

  .label{position:absolute;top:300px;width:270px;height:560px;background:var(--label);overflow:hidden;box-shadow:0 6px 14px rgba(0,0,0,.12)}
  .label.front{left:318px}
  .label.back{left:612px}
  .label .shoulder{position:absolute;left:0;top:0;width:100%;height:120px}
  .label .splash{position:absolute;top:150px;background:linear-gradient(180deg,var(--lime-pale),var(--leaf) 55%,var(--lime-soft))}
  .front .splash{right:0;width:70px;height:270px}
  .back .splash{right:76px;width:56px;height:260px}

  .vertical-name{position:absolute;left:40px;top:420px;transform:rotate(-90deg);transform-origin:left top;font-weight:700;font-size:54px;color:var(--leaf);white-space:nowrap;line-height:1}

  .calorie-badge{position:absolute;left:8px;top:440px;width:40px;height:56px;border:2px solid var(--leaf-dark);border-radius:6px;text-align:center;font-size:9px;line-height:1;padding-top:4px;color:var(--leaf-dark)}
  .calorie-badge b{display:block;font-size:20px;font-weight:700}
  .volume{position:absolute;left:8px;top:502px;font-size:13px;font-weight:700;color:var(--leaf-dark)}

  .flavour-name{position:absolute;left:58px;top:438px;font-weight:700;font-size:19px;color:var(--leaf-dark);border-bottom:2px solid var(--leaf-dark);padding-bottom:2px;width:200px;line-height:1.3}
  .claims{position:absolute;left:58px;top:470px;list-style:none;width:205px;font-family:"Share Tech Mono",monospace;font-size:10.5px}
  .claims li{display:flex;align-items:center;gap:6px;height:22px;border-bottom:1px solid var(--leaf)}
  .claims .mark{width:11px;height:11px;background:var(--leaf);color:#fff;font-size:9px;line-height:11px;text-align:center;flex:none}
  .claims .mark.dark{background:var(--ink)}

  .arabic{font-family:"Cairo",sans-serif;direction:rtl}
  .arabic-name{position:absolute;left:36px;top:400px;transform:rotate(-90deg);transform-origin:left top;white-space:nowrap;font-size:40px;color:var(--leaf-dark);line-height:1.2}
  .ingredients-head{position:absolute;left:14px;top:428px;width:200px;font-size:13px;border-bottom:2px solid var(--leaf-dark);padding:0 6px 2px 0;text-align:right;line-height:1.6}
  .ingredients{position:absolute;left:14px;top:456px;width:200px;list-style:none;font-size:11px}
  .ingredients li{display:flex;justify-content:space-between;align-items:center;gap:8px;height:22px;padding-right:6px;border-bottom:1px solid var(--leaf);white-space:nowrap}
  .ingredients .mark{width:11px;height:11px;background:var(--leaf);flex:none}

  .facts{position:absolute;right:8px;top:150px;width:62px;border:1px solid var(--ink);padding:4px;font-family:"Share Tech Mono",monospace;font-size:7.5px;line-height:1.3;background:var(--label)}
  .facts h3{font-size:9px;border-bottom:2px solid var(--ink);margin-bottom:3px;font-family:"Oswald",sans-serif}
  .facts p{border-bottom:1px solid #999}
</style>
</head>
<body>

<header class="title-block">
  <div class="heading">Label Design</div>
  <div class="kicker">VITAMIN</div>
  <div class="brand-line"><span class="dot"></span><span class="name">Qirna Vitamin</span></div>
  <div class="flavour-tag">POMOGRANITE CHERRY</div>
</header>

<section class="label front">
  <svg class="shoulder" viewBox="0 0 270 120" preserveAspectRatio="none">
    <path d="M0 0H270V70Q135 40 0 110Z" fill="var(--lime-soft)"/>
    <path d="M0 110Q135 40 270 70" fill="none" stroke="var(--leaf)" stroke-width="6"/>
  </svg>
  <div class="splash" role="img" aria-label="Green water splash with bubbles"></div>
  <div class="vertical-name">Qirna Vitamin</div>
  <div class="calorie-badge"><b>50</b>CALORIE</div>
  <div class="volume">500 ML</div>
  <div class="flavour-name">KIWI . STRAWBERRY</div>
  <ul class="claims">
    <li><span class="mark">+</span>Flavoured + Natural Flavour</li>
    <li><span class="mark dark">+</span>No Artificial Coloring Added</li>
    <li><span class="mark">+</span>Real Minirals &amp; Electrolytes</li>
  </ul>
</section>

<section class="label back">
  <svg class="shoulder" viewBox="0 0 270 120" preserveAspectRatio="none">
    <path d="M0 0H270V110Q135 40 0 70Z" fill="var(--lime-soft)"/>
    <path d="M0 70Q135 40 270 110" fill="none" stroke="var(--leaf)" stroke-width="6"/>
  </svg>
  <div class="splash" role="img" aria-label="Green water splash with bubbles"></div>
  <div class="arabic arabic-name">فيتامين قرنة</div>
  <div class="arabic ingredients-head">المكونات</div>
  <ul class="arabic ingredients">
    <li>نكهة طبيعية مضافة<span class="mark"></span></li>
    <li>بدون ألوان صناعية<span class="mark"></span></li>
    <li>معادن وأملاح حقيقية<span class="mark"></span></li>
  </ul>
  <div class="facts">
    <h3>Nutrition Facts</h3>
    <p>Calories 50</p>
    <p>Sugar 12g</p>
    <p>Sodium 110mg</p>
    <p>Potassium 45mg</p>
    <p>Vitamin C 100%</p>
    <p>Vitamin B3 25%</p>
    <p>Zinc 10%</p>
  </div>
</section>

</body>
</html>
```